Business Cards for new orthopaedic surgery practice

My husband and I are starting our own orthopaedic surgery practice. We are looking for a business card that is uniform, but one will have my name/title and the other will have his. You can just create one design with my name on it for now. But when I choose your design as the winning design I will ask that you add another copy with his name/title.

We are looking for classy, simple, elite all in one. We like dark blues/a little gold/yellow. Something that goes with our logo. We want our logo incorporated. Here is all the info you need:
Business name: RV Bone & Vitality Center
Location: 38517 North Willowmere Ave
Marlow Heights, FL 33990
Phone: 954-218-4063
Fax: 954-582-7341
Email: info@myrvbonecare.example

Names: Lydia Vance, M.D.
Board Certified Hand and Upper Extremity Surgeon

Ebo Dansu, M.D.
Board Certified Hip & Knee Replacement/General Orthopaedic Surgeon

Can decide what you want to put on the back. Maybe a slogan:
Rooted in Care. Focused on You

I am just going to upload our logo. The only thing is if we select you as the winning design, the location, and phone numbers may change. We will need your help to update that once fully solidified.

Industry/Entity Type

Medical

Contact Information for Business Card

Colors
0054AA
0677BA
7BADD7
CADEEF
E8F1F8
0094D4
00A9DD
6FCCEA
C7EBF8
E9F6FB

Requirements
Must have
• class, appeal,
Should not have
• We want to air on the side of masculine if we are looking at masculine vs. feminine feel. But we still want it classy, sophisticated, and something we will love

```html
<!DOCTYPE html>
<html lang="en">
<head>
<meta charset="utf-8">
<title>RV Bone &amp; Vitality Center — Business Card</title>
<link rel="stylesheet" href="https://fonts.googleapis.com/css2?family=Poppins:wght@500;700&family=Open+Sans:wght@400;600&display=swap">
<style>
  :root {
    --navy: #1f2f6e;
    --teal: #16a3c2;
    --card: #e9ecf2;
    --stage: #d5dae3;
    --ink: #1b1f2e;
  }
  * { box-sizing: border-box; margin: 0; padding: 0; }
  html, body { width: 1200px; height: 900px; overflow: hidden; }
  body {
    background: var(--stage);
    display: flex;
    flex-direction: column;
    align-items: center;
    justify-content: center;
    gap: 40px;
  }
  .card {
    position: relative;
    width: 700px;
    height: 400px;
    border-radius: 36px;
    background: var(--card);
    overflow: hidden;
    box-shadow: 0 10px 28px rgba(31, 47, 110, 0.18);
  }
  .card__waves { position: absolute; inset: 0; width: 100%; height: 100%; }

  /* Front */
  .brand {
    position: absolute;
    inset: 0;
    display: flex;
    align-items: center;
    justify-content: center;
    gap: 16px;
  }
  .brand__dot {
    width: 22px; height: 22px;
    border-radius: 50%;
    background: var(--navy);
  }
  .brand__name {
    font-family: "Poppins", sans-serif;
    font-weight: 700;
    font-size: 30px;
    color: var(--navy);
    letter-spacing: 0.5px;
  }

  /* Back */
  .contact {
    position: absolute;
    right: 48px;
    top: 50px;
    text-align: right;
  }
  .contact__name {
    font-family: "Poppins", sans-serif;
    font-weight: 700;
    font-size: 34px;
    color: var(--navy);
    letter-spacing: 1px;
    line-height: 1.1;
  }
  .contact__title {
    font-family: "Poppins", sans-serif;
    font-weight: 500;
    font-size: 11.5px;
    color: var(--teal);
    letter-spacing: 0.6px;
    margin-top: 4px;
  }
  .contact__list {
    list-style: none;
    margin-top: 30px;
    display: flex;
    flex-direction: column;
    gap: 12px;
  }
  .contact__item {
    display: flex;
    align-items: center;
    justify-content: flex-end;
    gap: 16px;
    font-family: "Open Sans", sans-serif;
    font-size: 19px;
    color: var(--ink);
    letter-spacing: 0.8px;
    line-height: 1.15;
  }
  .contact__icon {
    flex: none;
    width: 30px; height: 30px;
    border-radius: 50%;
    background: var(--navy);
    display: flex;
    align-items: center;
    justify-content: center;
  }
  .contact__icon svg { width: 16px; height: 16px; fill: #fff; }
</style>
</head>
<body>

  <section class="card card--front" aria-label="Card front">
    <svg class="card__waves" viewBox="0 0 700 400" preserveAspectRatio="none" aria-hidden="true">
      <path fill="var(--navy)" d="M0 0 H170 C150 70 85 120 75 210 C65 300 95 350 100 400 H0 Z"/>
      <path fill="var(--teal)" d="M0 0 H155 C130 70 65 120 55 210 C45 300 70 350 72 400 H0 Z"/>
      <path fill="var(--navy)" d="M700 0 H615 C585 60 600 130 640 185 C675 235 690 300 700 330 Z"/>
      <path fill="var(--teal)" d="M700 0 H640 C615 60 628 125 660 180 C688 228 697 280 700 300 Z"/>
    </svg>
    <div class="brand">
      <span class="brand__dot"></span>
      <span class="brand__name">RV Bone &amp; Vitality Center</span>
    </div>
  </section>

  <section class="card card--back" aria-label="Card back">
    <svg class="card__waves" viewBox="0 0 700 400" preserveAspectRatio="none" aria-hidden="true">
      <path fill="var(--teal)" d="M0 0 H150 C185 120 135 260 175 400 H0 Z"/>
      <path fill="var(--navy)" d="M135 0 H175 C210 120 160 260 200 400 H165 C125 260 172 120 135 0 Z"/>
    </svg>
    <div class="contact">
      <h1 class="contact__name">Lydia Vance, M.D.</h1>
      <p class="contact__title">Board Certified Hand and Upper Extremity Surgeon</p>
      <ul class="contact__list">
        <li class="contact__item">
          <span>954-218-4063</span>
          <span class="contact__icon"><svg viewBox="0 0 24 24"><path d="M6.6 10.8c1.4 2.8 3.8 5.1 6.6 6.6l2.2-2.2c.3-.3.7-.4 1-.2 1.1.4 2.3.6 3.6.6.6 0 1 .4 1 1V20c0 .6-.4 1-1 1C10.6 21 3 13.4 3 4c0-.6.4-1 1-1h3.5c.6 0 1 .4 1 1 0 1.3.2 2.5.6 3.6.1.3 0 .7-.2 1l-2.3 2.2z"/></svg></span>
        </li>
        <li class="contact__item">
          <span>954-582-7341</span>
          <span class="contact__icon"><svg viewBox="0 0 24 24"><path d="M6 2h12v5H6zM4 8h16a2 2 0 0 1 2 2v6h-4v6H6v-6H2v-6a2 2 0 0 1 2-2zm4 8v4h8v-4z"/></svg></span>
        </li>
        <li class="contact__item">
          <span>info@myrvbonecare.example</span>
          <span class="contact__icon"><svg viewBox="0 0 24 24"><path d="M2 5h20v14H2zm2 2v.5l8 5 8-5V7zm0 2.8V17h16V9.8l-8 5z"/></svg></span>
        </li>
        <li class="contact__item">
          <span>38517 North Willowmere Ave<br>Marlow Heights, FL 33990</span>
          <span class="contact__icon"><svg viewBox="0 0 24 24"><path d="M12 2a7 7 0 0 0-7 7c0 5 7 13 7 13s7-8 7-13a7 7 0 0 0-7-7zm0 9.5A2.5 2.5 0 1 1 12 6.5a2.5 2.5 0 0 1 0 5z"/></svg></span>
        </li>
      </ul>
    </div>
  </section>

</body>
</html>
```